New Business Card Design Project

We require a business card design for Vexalund, a newly established Indian company.
Our focus is on the development, manufacturing, and export of a diverse array of pharmaceutical products on a global scale. The card should convey a professional appearance, as our primary markets are in Africa, China, and Southeast Asian nations.
We envision a two-sided business card, with the reverse side dedicated to a logo set against a solid color or an elegantly designed pattern. The corners should be rounded. We would appreciate seeing both horizontal and vertical design options. We trust the designer to utilize their expertise in creating this design.

The content for the business card is included in the attached Word file.

Target Market(s)

Our primary markets are in Africa, China, and Southeast Asian, Latin America, Maldives, Sri Lanka

Industry/Entity Type

Pharmaceutical Manufacturing and Export

Contact Information for Business Card

Colors

Designer to choose colors to be used in the design.

Requirements
Must have
• The reverse side of the business card features solely the logo along with the tagline, "Care for Every Day."
Should not have
• The logo should not exceed two instances, encompassing both the front and back sides of the card.

```html
<!DOCTYPE html>
<html lang="en">
<head>
<meta charset="utf-8">
<title>Vexalund Business Card</title>
<link href="https://fonts.googleapis.com/css2?family=Lato:ital,wght@0,400;0,700;0,900;1,400&family=Lora:ital@1&display=swap" rel="stylesheet">
<style>
  :root {
    --stage: #2b2d31;
    --brand-blue: #29a8e0;
    --accent-red: #ef4b3c;
    --paper: #ffffff;
    --ink: #4a4a4a;
    --ink-soft: #6b6b6b;
    --faint: #efefef;
  }
  html, body {
    margin: 0;
    width: 1200px;
    height: 952px;
    overflow: hidden;
    background: var(--stage);
    font-family: "Lato", sans-serif;
  }
  .stage {
    position: relative;
    width: 1200px;
    height: 952px;
  }
  .card {
    position: absolute;
    left: 300px;
    width: 600px;
    height: 343px;
    border-radius: 14px;
    overflow: hidden;
    box-shadow: 0 10px 30px rgba(0,0,0,0.45);
  }
  .card-front { top: 96px; background: var(--paper); }
  .card-back  { top: 510px; background: var(--brand-blue); }

  .front-band {
    position: absolute;
    inset: 0;
  }
  .holder {
    position: absolute;
    left: 150px;
    top: 38px;
  }
  .holder-name {
    margin: 0;
    font-weight: 700;
    font-size: 28px;
    letter-spacing: 1px;
    color: var(--brand-blue);
  }
  .holder-name .surname { color: var(--accent-red); }
  .holder-role {
    margin: 2px 0 0;
    font-size: 19px;
    color: var(--ink-soft);
  }
  .contact-list {
    position: absolute;
    left: 62px;
    top: 118px;
    margin: 0;
    padding: 0;
    list-style: none;
    font-size: 14px;
  }
  .contact-item {
    display: flex;
    align-items: flex-start;
    gap: 10px;
    line-height: 1.3;
  }
  .contact-item + .contact-item { margin-top: 10px; }
  .contact-item.address { color: var(--ink); font-size: 13px; margin-bottom: 16px; }
  .contact-item.on-band { color: var(--paper); }
  .contact-icon {
    flex: none;
    width: 18px;
    height: 18px;
    border-radius: 3px;
    display: flex;
    align-items: center;
    justify-content: center;
  }
  .icon-blue { background: var(--brand-blue); }
  .icon-red  { background: var(--accent-red); }

  .faint-mark {
    position: absolute;
    right: 60px;
    top: 150px;
    width: 150px;
    height: 150px;
    border-radius: 50%;
    background: var(--faint);
  }

  .back-lockup {
    position: absolute;
    inset: 0;
    display: flex;
    flex-direction: column;
    align-items: center;
    justify-content: center;
    color: var(--paper);
  }
  .wordmark {
    display: flex;
    align-items: center;
    gap: 14px;
  }
  .wordmark-dot {
    width: 26px;
    height: 26px;
    border-radius: 50%;
    background: var(--paper);
  }
  .wordmark-name {
    font-weight: 900;
    font-size: 52px;
    letter-spacing: 0.5px;
  }
  .tagline {
    display: flex;
    align-items: center;
    gap: 10px;
    margin-top: 4px;
    font-family: "Lora", serif;
    font-style: italic;
    font-size: 22px;
  }
  .tagline-rule {
    width: 46px;
    height: 1.5px;
    background: var(--paper);
  }
</style>
</head>
<body>
<main class="stage">

  <section class="card card-front" aria-label="Card front">
    <svg class="front-band" width="600" height="343" viewBox="0 0 600 343" aria-hidden="true">
      <path d="M0 168 H345 L300 262 Q296 270 286 270 H0 Z" fill="var(--brand-blue)"/>
    </svg>
    <div class="faint-mark" aria-hidden="true"></div>

    <div class="holder">
      <h1 class="holder-name">ARJUN K. <span class="surname">TALWAR</span></h1>
      <p class="holder-role">CEO/Vexalund</p>
    </div>

    <ul class="contact-list">
      <li class="contact-item address">
        <span class="contact-icon icon-blue">
          <svg width="10" height="12" viewBox="0 0 10 12"><path d="M5 0a4 4 0 0 1 4 4c0 3-4 8-4 8S1 7 1 4a4 4 0 0 1 4-4z" fill="#fff"/><circle cx="5" cy="4" r="1.5" fill="var(--brand-blue)"/></svg>
        </span>
        <span>12, Lotus Nagar, Nashik,<br>422001, India</span>
      </li>
      <li class="contact-item on-band">
        <span class="contact-icon icon-red">
          <svg width="11" height="11" viewBox="0 0 12 12"><path d="M2 1l2.5 0 1 3-1.5 1a7 7 0 0 0 3 3l1-1.5 3 1V10a1 1 0 0 1-1 1C5 11 1 7 1 2a1 1 0 0 1 1-1z" fill="#fff"/></svg>
        </span>
        <span>+919876543210</span>
      </li>
      <li class="contact-item on-band">
        <span class="contact-icon icon-red">
          <svg width="12" height="9" viewBox="0 0 12 9"><rect x="0.5" y="0.5" width="11" height="8" fill="none" stroke="#fff"/><path d="M0.5 0.5L6 5l5.5-4.5" fill="none" stroke="#fff"/></svg>
        </span>
        <span>atalwar@vexalund.com</span>
      </li>
      <li class="contact-item on-band">
        <span class="contact-icon icon-red">
          <svg width="10" height="10" viewBox="0 0 10 10"><path d="M5 0L9 9 5 7 1 9z" fill="#fff"/></svg>
        </span>
        <span>atalwar@vexalund.com</span>
      </li>
    </ul>
  </section>

  <section class="card card-back" aria-label="Card back">
    <div class="back-lockup">
      <div class="wordmark">
        <span class="wordmark-dot" aria-hidden="true"></span>
        <span class="wordmark-name">Vexalund</span>
      </div>
      <div class="tagline">
        <span class="tagline-rule" aria-hidden="true"></span>
        <span>Care for Every Day</span>
        <span class="tagline-rule" aria-hidden="true"></span>
      </div>
    </div>
  </section>

</main>
</body>
</html>
```